Email signatures and letterhead for in-house lawyers and staff

I need Word, Outlook, and Gmail compatible letterhead and email signature block for an in-house litigation group. Simple and generic is the goal! The design must be user-modifiable for several locations and job titles. The design will work best if created in MS Word. We are an in-house group of trial lawyers, about 40 persons total, operating from nine locations, and providing services in ten US states. Letterhead will be used in header of MSWord documents. Email sig will be used in both Outlook and Gmail. The office name will be different in each of our locations, so the design has to be user-modifiable.

Industry/Entity Type

Law Firm

Font styles to use
Sans Serif

Requirements
Must have
• A fresher, more professional look than the screenshots I've posted

The screenshot with multiple attorney names in the office is most representative of the info we want included.
Nice to have
• Sylish but not overly so. Generic legal symbols might be appropriate, but can't look like tired old clip art.
Should not have
• watermarks

```html
<!DOCTYPE html>
<html lang="en">
<head>
<meta charset="utf-8">
<title>Law Office Letterhead and Email Signature</title>
<link href="https://fonts.googleapis.com/css2?family=Fira+Sans:wght@400;500;600&family=Fira+Sans+Condensed:wght@400;500;600&display=swap" rel="stylesheet">
<style>
  :root{
    --blue:#2a55b5;
    --brown:#a0733a;
    --brown-dark:#6b4a24;
    --ink:#2b2b2b;
    --paper:#ffffff;
    --stage:#ffffff;
    --edge:#d9d9d9;
    --sig-fill:#e3eaf8;
  }
  *{margin:0;padding:0;box-sizing:border-box}
  html,body{width:1200px;height:1200px;overflow:hidden;background:var(--stage)}
  body{position:relative;font-family:"Fira Sans Condensed","Fira Sans",sans-serif;color:var(--ink)}

  .letterhead{position:absolute;left:102px;top:146px;width:724px;height:938px;background:var(--paper);border:1px solid var(--edge)}
  .firm-title{position:absolute;left:43px;top:36px;font-family:"Fira Sans",sans-serif;font-weight:500;font-size:22px;letter-spacing:1.5px;color:var(--blue)}
  .firm-mark{position:absolute;left:40px;top:80px;width:44px;height:44px;background:var(--blue)}
  .partner-list{position:absolute;left:107px;top:74px;list-style:none;font-size:15.5px;line-height:19.5px;color:var(--brown)}
  .contact{position:absolute;right:38px;top:42px;text-align:right;font-size:11.5px;line-height:19px}
  .contact dt{display:inline;color:var(--brown)}
  .contact dd{display:inline;color:var(--ink)}
  .contact .row{display:block}
  .address{position:absolute;right:38px;top:104px;text-align:right;font-size:11.5px;line-height:17px;font-style:normal}
  .recipient{position:absolute;left:67px;top:230px;font-size:13px;line-height:26.5px;font-weight:500}
  .body-copy{position:absolute;left:67px;width:575px;font-size:13.4px;line-height:26.5px;font-weight:500;text-align:justify}
  .body-copy.p1{top:338px}
  .body-copy.p2{top:497px}
  .closing{position:absolute;left:72px;top:696px;font-size:13px;font-weight:500}
  .signature-art{position:absolute;background:var(--sig-fill);border-radius:3px}
  .letterhead .signature-art{left:72px;top:718px;width:230px;height:38px}
  .footer-band{position:absolute;left:0;bottom:0;width:100%;height:28px}

  .email-signature{position:absolute;left:464px;top:640px;width:658px;height:259px;background:var(--paper);border:1px solid var(--edge);overflow:hidden}
  .email-signature .signature-art{left:44px;top:20px;width:220px;height:32px}
  .job-title{position:absolute;left:50px;top:56px;font-size:14px;color:var(--brown)}
  .sig-details{position:absolute;left:44px;top:82px;font-size:8.6px;line-height:13px;list-style:none;color:var(--ink)}
  .sig-rule{position:absolute;left:24px;top:144px;width:602px;height:10px}
  .sig-mark{position:absolute;left:480px;top:100px;width:140px;height:101px}
  .disclaimer{position:absolute;left:30px;top:162px;width:430px;font-size:5.6px;line-height:11.5px;font-weight:600}
  .disclaimer p+p{margin-top:7px}
  .email-signature .footer-band{height:19px}
</style>
</head>
<body>

<section class="letterhead" aria-label="Letterhead">
  <h1 class="firm-title">LAW OFFICE OF</h1>
  <span class="firm-mark" aria-hidden="true"></span>
  <ul class="partner-list">
    <li>Daniel R. Hale</li>
    <li>Laura E. Benton</li>
    <li>Mark T. Whitfield</li>
  </ul>
  <dl class="contact">
    <span class="row"><dt>Phone : </dt><dd>555 -010 -2222</dd></span>
    <span class="row"><dt>Fax : </dt><dd>555 -010 -3333</dd></span>
    <span class="row"><dt>Email : </dt><dd>&nbsp;counsel@example-law.com</dd></span>
  </dl>
  <address class="address">4100 Harbor Road West, Suite 210<br>Lakeview, ZZ 00000</address>

  <div class="recipient">To<br>The,<br>Director</div>

  <p class="body-copy p1">Lorem ipsum dolor sit amet, consectetur adipiscing elit. Sed at ante. Mauris eleifend, quam a vulptate dictum, massa quam dapibus leo, eget vulputate orci purus ut lorem. In fringilla mi in ligula. Pellen tesque aliquam quam vel dolor. Nunc adipiscing. Sed quamodio, tempus ac, aliquam molestie varius ac, tellus. Vestibulum ut nulla aliquam risus rutrum interdum. Pellen-tesque lorem.</p>
  <p class="body-copy p2">Curabitur sit amet erat quis risus feugiat viverra. Pellentesque augue justo, sagittis et, lacinia at, venenatis non, arcu. Nunc nec libero. In cursus dictum risus. Etiam tristique nisl a nulla. Ut a orci. Curabitur dolonunc,egestas at, accumsan at, malesuada nec, magna. Nulla facilisi. Nunc volutpat. Vestibulum ante ipsum primis in faucibus orci luctus et ultrices posuere cubilia Curae. Ut sit amet orci vel mauris blandit vehicula. Nullam quis enim. Integer dignissim viverra velit. Curabitur in odio.</p>

  <p class="closing">Thanking you,</p>
  <div class="signature-art" role="img" aria-label="Handwritten signature of Daniel R. Hale in blue ink"></div>

  <svg class="footer-band" viewBox="0 0 724 28" preserveAspectRatio="none" aria-hidden="true">
    <polygon points="0,13 425,13 418,28 0,28" fill="var(--blue)"/>
    <polygon points="444,0 724,0 724,28 426,28" fill="var(--brown)"/>
  </svg>
</section>

<section class="email-signature" aria-label="Email signature">
  <div class="signature-art" role="img" aria-label="Handwritten signature of Daniel R. Hale in blue ink"></div>
  <p class="job-title">Attorney at law</p>
  <ul class="sig-details">
    <li>Law Office Of Daniel R. Hale</li>
    <li>T: 555.020.1111| F: 555.020.4444</li>
    <li>daniel.hale@example-trial.com</li>
    <li>2850 Cedar Ave. North - Suite 410, Lakeview, ZZ 00000</li>
  </ul>
  <svg class="sig-rule" viewBox="0 0 602 10" preserveAspectRatio="none" aria-hidden="true">
    <rect x="0" y="0" width="602" height="10" rx="4" fill="var(--blue)"/>
  </svg>
  <svg class="sig-mark" viewBox="0 0 140 101" aria-hidden="true">
    <polygon points="0,54 10,101 10,54" fill="var(--brown-dark)"/>
    <polygon points="118,0 140,44 118,44" fill="var(--brown-dark)"/>
    <rect x="10" y="0" width="108" height="101" fill="var(--brown)"/>
  </svg>
  <div class="disclaimer">
    <p>The information contained in this communication from the sender is confidential. It is intended solely for use by the recipient and others authorized to receive it. If you are not the recipient, you are hereby notified that any disclosure, copying, distribution, or taking action in relation to the contents of this information is strictly prohibited and may be unlawful.</p>
    <p>The Law Office of Carl J. Render is an unincorporated association of individual licensed attorneys employed by Northfield Mutual Insurance Companies for the purpose of representing Northfield Mutual Insurance Companies, its policyholders, and insureds.</p>
  </div>
  <svg class="footer-band" viewBox="0 0 658 19" preserveAspectRatio="none" aria-hidden="true">
    <polygon points="0,7 382,7 372,19 0,19" fill="var(--blue)"/>
    <polygon points="398,0 658,0 658,19 380,19" fill="var(--brown)"/>
  </svg>
</section>

</body>
</html>
```